Business card, Invoice and printable service brochure

I need a 5.5x8.5 invoice, business card and printable service template for reception desk designed for my Rug repair, restoration and cleaning business.

I have included a picture for reference

www.velborenrug.example

Columns i need in my invoice:
Type of rug, Size, Background Color, Repair needs, Notes, Price and rug cleaning disclaimer.

Target Market(s)

Higher segment clients

Industry/Entity Type

Rug Repair, Restoration and cleaning,

Requirements
Must have
• Services hast to be listed on the invoice as well as service brochure.

```html
<!DOCTYPE html>
<html lang="en">
<head>
<meta charset="utf-8">
<title>Velboren Rug – Invoice</title>
<link rel="stylesheet" href="https://fonts.googleapis.com/css2?family=Archivo:wght@400;500;700;900&display=swap">
<style>
  :root {
    --navy: #272b38;
    --gold: #c2992e;
    --brand-gold: #b89a66;
    --ink: #2a2a2a;
    --rule: #c8c8c8;
    --paper: #ffffff;
    --backdrop: #7fcdec;
  }
  * { margin: 0; padding: 0; box-sizing: border-box; }
  html, body { width: 1200px; height: 1200px; overflow: hidden; }
  body { background: var(--backdrop); font-family: "Archivo", Arial, sans-serif; color: var(--ink); }

  .invoice { position: absolute; left: 198px; top: 30px; width: 803px; height: 1140px; background: var(--paper); overflow: hidden; }
  .invoice > * { position: absolute; }

  .header-band { left: 0; top: 0; width: 500px; height: 149px; }
  .brand-name { left: 0; width: 500px; top: 40px; text-align: center; font-size: 50px; font-weight: 500; letter-spacing: 1px; color: var(--brand-gold); }
  .brand-tagline { left: 0; width: 500px; top: 102px; text-align: center; font-size: 12px; letter-spacing: 4.5px; color: var(--brand-gold); }

  .billing-label { left: 81px; top: 221px; font-size: 11px; }
  .billing-name { left: 81px; top: 233px; font-size: 19px; font-weight: 700; }
  .doc-title { left: 517px; top: 217px; font-size: 32px; font-weight: 900; letter-spacing: 4px; color: #000; }
  .title-rule { left: 81px; top: 262px; width: 648px; height: 2px; background: var(--gold); }

  .client-details { left: 81px; top: 274px; font-size: 12px; line-height: 15px; }
  .invoice-meta { left: 517px; top: 274px; font-size: 11px; line-height: 15px; display: grid; grid-template-columns: 71px auto; }

  .items-head-desc { left: 0; top: 359px; width: 381px; height: 61px; background: var(--gold); color: #fff; font-weight: 700; font-size: 14px; display: flex; align-items: center; padding-left: 169px; padding-top: 14px; }
  .items-head-cols { left: 381px; top: 377px; width: 422px; height: 39px; background: var(--navy); color: #fff; font-weight: 700; font-size: 14px; display: grid; grid-template-columns: 123px 124px 175px; }
  .items-head-cols span { display: flex; align-items: center; justify-content: center; border-left: 1px solid #fff; }
  .items-head-cols span:first-child { border-left: 0; }
  .items-head-cols span:last-child { justify-content: flex-start; padding-left: 23px; }

  .items { left: 0; top: 420px; width: 800px; border-collapse: collapse; font-size: 14px; }
  .items td { height: 43.6px; border-bottom: 1px solid var(--rule); vertical-align: middle; letter-spacing: 0.3px; }
  .items .num { width: 122px; text-align: center; padding-left: 16px; }
  .items .desc { width: 259px; padding-left: 17px; }
  .items .rate { width: 123px; text-align: center; border-left: 1px solid var(--rule); }
  .items .qty { width: 124px; text-align: center; border-left: 1px solid var(--rule); }
  .items .amount { text-align: left; padding-left: 43px; border-left: 1px solid var(--rule); }
  .items tr:first-child .desc { border-left: 1px solid var(--rule); }
  .items tr + tr .desc { border-left: 1px solid var(--rule); }

  .totals { left: 538px; top: 774px; width: 190px; font-size: 13px; line-height: 16px; display: grid; grid-template-columns: 113px auto; }
  .totals .label { text-align: center; }
  .totals-rule { left: 538px; top: 817px; width: 190px; height: 2px; background: var(--rule); }
  .total-box { left: 537px; top: 836px; width: 190px; height: 30px; border: 1px solid var(--navy); display: grid; grid-template-columns: 97px auto; font-weight: 700; font-size: 16px; }
  .total-box .label { background: var(--navy); color: #fff; display: flex; align-items: center; justify-content: center; }
  .total-box .value { display: flex; align-items: center; padding-left: 16px; }

  .section-title { left: 81px; font-size: 16px; font-weight: 700; color: var(--gold); letter-spacing: 0.3px; }
  .payment-title { top: 803px; }
  .payment-lines { left: 81px; top: 827px; font-size: 13px; line-height: 16.5px; }
  .terms-title { top: 912px; }
  .terms-text { left: 81px; top: 939px; font-size: 11.5px; }

  .signature-rule { left: 546px; top: 955px; width: 180px; height: 1px; background: #999; }
  .signature-name { left: 546px; top: 960px; width: 180px; text-align: center; font-size: 16px; }

  .contact { top: 1037px; display: flex; align-items: center; gap: 16px; font-size: 12.5px; line-height: 16px; }
  .contact svg { width: 36px; height: 36px; flex: none; }
  .contact-address { left: 84px; }
  .contact-phone { left: 338px; font-size: 11.5px; }
  .contact-web { left: 550px; }

  .footer-band { left: 0; top: 1096px; width: 803px; height: 44px; }
</style>
</head>
<body>
<main class="invoice">
  <svg class="header-band" viewBox="0 0 500 149" aria-hidden="true">
    <path d="M0 0 H500 L458 110 Q440 149 405 149 H0 Z" fill="var(--navy)"/>
  </svg>
  <div class="brand-name">VELBOREN RUG</div>
  <div class="brand-tagline">REPAIR | RESTORATION | CLEANING</div>

  <div class="billing-label">BILLING TO:</div>
  <div class="billing-name">CUSTOMER</div>
  <div class="doc-title">INVOICE</div>
  <div class="title-rule"></div>

  <div class="client-details">000 000 000<br>contact@example.com<br>Adderss, city</div>
  <div class="invoice-meta">
    <span>Invoice</span><span>: 00000</span>
    <span>Date</span><span>: 01 February,2021</span>
    <span>Due Date</span><span>: 01 February,2022</span>
  </div>

  <div class="items-head-desc">ITEM DESCRIPTION</div>
  <div class="items-head-cols"><span>RATE</span><span>QTY</span><span>AMOUNT</span></div>
  <table class="items">
    <tr><td class="num">1</td><td class="desc">TYPE OF RUG</td><td class="rate">1</td><td class="qty">$00</td><td class="amount">$00</td></tr>
    <tr><td class="num">2</td><td class="desc">SIZE</td><td class="rate">1</td><td class="qty">$00</td><td class="amount">$00</td></tr>
    <tr><td class="num">3</td><td class="desc">BACKGROUND COLOR</td><td class="rate">1</td><td class="qty">$00</td><td class="amount">$00</td></tr>
    <tr><td class="num">4</td><td class="desc">REPAIR NEEDS</td><td class="rate">1</td><td class="qty">$00</td><td class="amount">$00</td></tr>
    <tr><td class="num">5</td><td class="desc">NOTES</td><td class="rate">1</td><td class="qty">$00</td><td class="amount">$00</td></tr>
    <tr><td class="num">6</td><td class="desc">PRICE</td><td class="rate">1</td><td class="qty">$00</td><td class="amount">$00</td></tr>
    <tr><td class="num">7</td><td class="desc">RUG CLEANING DISCLAIMER</td><td class="rate">1</td><td class="qty">$00</td><td class="amount">$00</td></tr>
  </table>

  <div class="totals">
    <span class="label">SUBTOTAL</span><span>$00</span>
    <span class="label">TAX VAT 15%</span><span>0.0%</span>
  </div>
  <div class="totals-rule"></div>
  <div class="total-box"><span class="label">TOTAL</span><span class="value">$00</span></div>

  <div class="section-title payment-title">PAYMENT METHOD</div>
  <div class="payment-lines">ACCOUNT : (555)014-2290<br>SWIFT &nbsp;: (555)014-2290<br>ONLINE PAY : INFO@VELBORENRUG.EXAMPLE</div>
  <div class="section-title terms-title">TERMS &amp; CONDITIONS</div>
  <div class="terms-text">LOREM IPSUM DOLOR SIT AMET</div>

  <div class="signature-rule"></div>
  <div class="signature-name">Velboren</div>

  <div class="contact contact-address">
    <svg viewBox="0 0 36 36" aria-hidden="true">
      <circle cx="18" cy="18" r="16.5" fill="none" stroke="var(--gold)" stroke-width="1.5"/>
      <path d="M18 27 C13 21 12 18 12 15.5 A6 6 0 0 1 24 15.5 C24 18 23 21 18 27 Z" fill="none" stroke="var(--gold)" stroke-width="1.5"/>
      <circle cx="18" cy="15.5" r="2.3" fill="none" stroke="var(--gold)" stroke-width="1.5"/>
    </svg>
    <span>1200 Harrow Lane,<br>Brookvale, IL 60000</span>
  </div>
  <div class="contact contact-phone">
    <svg viewBox="0 0 36 36" aria-hidden="true">
      <circle cx="18" cy="18" r="16.5" fill="none" stroke="var(--gold)" stroke-width="1.5"/>
      <path d="M12.5 10.5 L15.5 10 L17 14.5 L15 16 C16 18.5 17.5 20 20 21 L21.5 19 L26 20.5 L25.5 23.5 C24.5 25.5 22 25.8 19 24.5 C15.5 23 13 20.5 11.5 17 C10.3 14 10.5 11.8 12.5 10.5 Z" fill="none" stroke="var(--gold)" stroke-width="1.5" stroke-linejoin="round"/>
    </svg>
    <span>(555)014-2290<br>(555)014-2290</span>
  </div>
  <div class="contact contact-web">
    <svg viewBox="0 0 36 36" aria-hidden="true">
      <circle cx="18" cy="18" r="16.5" fill="none" stroke="var(--gold)" stroke-width="1.5"/>
      <g fill="none" stroke="var(--gold)" stroke-width="1.3">
        <circle cx="18" cy="18" r="9"/>
        <ellipse cx="18" cy="18" rx="4" ry="9"/>
        <path d="M9 18 H27 M10.5 13.5 H25.5 M10.5 22.5 H25.5"/>
      </g>
    </svg>
    <span>info@velborenrug.example<br>www.velborenrug.example</span>
  </div>

  <svg class="footer-band" viewBox="0 0 803 44" preserveAspectRatio="none" aria-hidden="true">
    <path d="M480 44 Q500 13 560 13 H720 Q760 13 780 44 Z" fill="var(--navy)"/>
    <path d="M0 0 H450 Q505 0 520 44 H0 Z" fill="var(--gold)"/>
  </svg>
</main>
</body>
</html>
```